Facebook Header Design Project.

I'm supplying white and colored logos. The Facebook page already exists. URL = https://www.brindlepost.example/quillarc.studio The design should not be based on what's already there. Consider mobile implications of the design. This Design will form the designs of other social media headers. QuillArc is a web design | digital marketing company.

Target Market(s)

People interested in web design | digital marketing services.

Industry/Entity Type

QuillArc is a web design | digital marketing company. That should be clear in the design.

Colors
0054AA
0677BA
7BADD7
CADEEF
E8F1F8

Requirements
Must have
• Logo. Use Facebook header image dimension.
Nice to have
• Use a color scheme like the logo and feel free to add a color or two from the other side of the color whee.

```html
<!DOCTYPE html>
<html lang="en">
<head>
<meta charset="utf-8">
<title>QuillArc – Header Designs</title>
<link rel="stylesheet" href="https://fonts.googleapis.com/css2?family=Roboto+Condensed:wght@400;700&family=Oswald:wght@400&family=Josefin+Sans:wght@600&family=Playball&family=Lato:wght@400;700&display=swap">
<style>
  :root{
    --stage:#537592;
    --brand-deep:#0054AA;
    --brand-mid:#0677BA;
    --brand-soft:#7BADD7;
    --brand-pale:#CADEEF;
    --brand-mist:#E8F1F8;
    --ink-navy:#2B4A8E;
    --night:#0B2A5C;
    --night-2:#0A3A78;
    --royal:#1C3897;
    --royal-2:#1F4FB5;
    --cyan:#18C8F0;
    --white:#FFFFFF;
  }
  *{margin:0;padding:0;box-sizing:border-box}
  html,body{width:1066px;height:1200px;overflow:hidden;background:var(--stage)}
  .canvas{position:relative;width:1066px;height:1200px}
  .header{position:absolute;left:111px;width:844px;height:312px;overflow:hidden;box-shadow:0 8px 16px rgba(0,0,0,.25)}
  .header--light{top:79px;background:var(--white)}
  .header--night{top:441px;background:linear-gradient(90deg,var(--night) 0%,var(--night-2) 100%)}
  .header--royal{top:804px;background:var(--royal)}

  .brand{position:absolute;font-family:"Lato",sans-serif;font-weight:700;font-size:30px;letter-spacing:.5px;line-height:1}
  .photo{position:absolute}
  .copy{position:absolute;font-family:"Lato",sans-serif;font-size:10.5px;line-height:1.35;color:var(--white);width:320px}
  .socials{position:absolute;display:flex;gap:13px}
  .socials span{width:15px;height:15px;border-radius:50%;background:var(--white)}

  /* header 1 */
  .header--light .photo{left:360px;top:0;width:484px;height:312px;
    background:linear-gradient(90deg,rgba(255,255,255,1) 0%,rgba(235,235,235,.6) 25%,#cfcfcf 55%,#9a9a9a 100%)}
  .header--light .title-band{position:absolute;left:0;top:74px;width:480px;height:120px;
    background:linear-gradient(90deg,var(--brand-soft) 0%,var(--brand-pale) 12%,rgba(255,255,255,0) 40%)}
  .header--light .foot-band{position:absolute;left:0;top:244px;width:844px;height:68px;
    background:linear-gradient(90deg,var(--brand-mid) 0%,#5EB2D6 35%,rgba(232,241,248,.6) 58%,rgba(255,255,255,0) 72%)}
  .header--light .brand{left:44px;top:24px;color:var(--brand-deep)}
  .header--light .line-1{position:absolute;left:45px;top:80px;font-family:"Roboto Condensed",sans-serif;font-weight:700;font-size:46px;color:var(--ink-navy);line-height:1}
  .header--light .line-2{position:absolute;left:45px;top:129px;font-family:"Oswald",sans-serif;font-weight:400;font-size:54px;line-height:1;
    color:transparent;-webkit-text-stroke:1.6px var(--brand-mid)}
  .header--light .copy{left:43px;top:260px}

  /* header 2 */
  .header--night .photo{left:488px;top:0;width:356px;height:312px;
    background:linear-gradient(120deg,#2F6B86 0%,#4C7F95 40%,#1E3A66 75%,#17294F 100%)}
  .header--night .brand{left:62px;top:30px;color:var(--white)}
  .header--night .headline{position:absolute;left:60px;top:78px;font-family:"Roboto Condensed",sans-serif;color:var(--white);font-size:47px;line-height:47px}
  .header--night .headline b{font-weight:700;display:block}
  .header--night .headline span{font-weight:400;display:block}
  .header--night .copy{left:60px;top:229px;font-size:11px}
  .header--night .socials{left:69px;top:292px}

  /* header 3 */
  .header--royal .shapes{position:absolute;inset:0}
  .header--royal .brand{left:44px;top:22px;color:var(--white)}
  .header--royal .headline{position:absolute;left:40px;top:84px;font-family:"Josefin Sans",sans-serif;font-weight:600;color:var(--white);font-size:33px;line-height:40px}
  .header--royal .script{position:absolute;left:40px;top:150px;font-family:"Playball",cursive;font-size:52px;color:var(--white);line-height:1}
  .header--royal .copy{left:40px;top:220px}
  .header--royal .socials{left:41px;top:282px;gap:17px}
</style>
</head>
<body>
<main class="canvas">

  <section class="header header--light">
    <div class="photo" role="img" aria-label="Top-down black and white photo of a desk with a laptop, hands typing, notebook and coffee cup"></div>
    <div class="title-band"></div>
    <div class="foot-band"></div>
    <div class="brand">QuillArc</div>
    <h1 class="line-1">WEB DESIGN &amp;</h1>
    <h2 class="line-2">DIGITAL MARKETING</h2>
    <p class="copy">Lorem Ipsum is simply dummy text of the printing and typesetting industry. Lorem has been the industry's standard dummy text ever since the 1500s</p>
  </section>

  <section class="header header--night">
    <div class="photo" role="img" aria-label="Photo of a smiling man at a desk celebrating while looking at his phone beside a laptop"></div>
    <div class="brand">QuillArc</div>
    <h1 class="headline"><b>WEB DESIGN &amp;</b><span>DIGITAL MARKETING</span><span>SERVICES</span></h1>
    <p class="copy">Lorem Ipsum is simply dummy text of the printing and typesetting industry. Lorem has been the industry's standard dummy text ever since the 1500s</p>
    <div class="socials" aria-label="Social links"><span></span><span></span><span></span><span></span></div>
  </section>

  <section class="header header--royal">
    <svg class="shapes" width="844" height="312" viewBox="0 0 844 312" aria-hidden="true">
      <path d="M234 0 H500 V70 Q430 75 380 80 Q300 82 250 60 Q234 40 234 0 Z" fill="#1F55B8"/>
      <path d="M352 312 L380 312 L400 312 L520 312 L432 170 Q392 110 405 85 Q420 50 500 30 L520 0 L480 0 Q400 30 385 70 Q370 110 400 170 Z" fill="#2E6BF2"/>
      <path d="M480 0 H535 Q430 40 414 80 Q405 100 420 130 L412 118 Q395 90 405 70 Q420 30 480 0 Z" fill="var(--cyan)"/>
      <path d="M535 0 H844 V312 H520 L432 170 Q408 128 415 95 Q425 55 480 35 Q510 20 535 0 Z" fill="#D7DBE0"/>
    </svg>
    <div class="photo" role="img" aria-label="Photo of a smiling man in a denim shirt working on a laptop at a table with a mug and plant"
         style="left:520px;top:20px;width:324px;height:292px;background:linear-gradient(160deg,#E2E4E7 0%,#C9CDD2 45%,#7E9DBF 70%,#E9EAEC 100%);clip-path:polygon(8% 0,100% 0,100% 100%,0 100%,-20% 50%)"></div>
    <div class="brand">QuillArc</div>
    <h1 class="headline">WEB DESIGN &amp;<br>DIGITAL MARKETING</h1>
    <div class="script">Services</div>
    <p class="copy">Lorem Ipsum is simply dummy text of the printing and typesetting industry. Lorem has been the industry's standard dummy text ever since the 1500s</p>
    <div class="socials" aria-label="Social links"><span></span><span></span><span></span><span></span></div>
  </section>

</main>
</body>
</html>
```